Meadow Pantry Brand Presentation

Looking for a brand presentation for Meadow Pantry. A business with three stores in Hackney, Clapham and Kings Cross and two booming e-commerce sites www.grainparcel.co.uk and www.vitalcratehub.co.uk.

The presentation should highlight the two online brands under the Meadow Pantry umbrella- VitalCrateHub and GrainParcel- as well as Meadow Pantry itself.

The presentation should give an overview of the history of the business, how fast it is growing and highlight the potential for growth.

Starting as a family run store, Meadow Fresh, in Hackney 7 years ago we have now expanded to 3 stores and 2 online sites with a turnover of 4m a year as well as collaborating with leading brands in the health foods sector such as Brightly Marnie, Pippas Cocoaloops, Plump Pulse co and Vorn.

The presentation should present us as a challenger to highstreet stores with a selective eye for incubating up and coming brands and providing high quality produce and products to our customer. It should also highlight the benefits of independent chains, we have communities around our stores of customers and brands.

Please include our positive attitude to sustainability: we run save-the-surplus in all our stores, have purlia refil stations, make our own juice out of wonky fruit and are selective in working with innivotive, ethical and eco-friendly brands.

Add a section on customer demographics. Mention that across our stores we have a wide range of customers: young professionals, gym/health consicious coming in for supplements & protein, young families focussed on healthy living buying baby food, fresh fruit & veg, young foodies.

We have plans to expand our London locations and would like this deck to help us compete with locations highstreet brands are fighting for. We also plan to start our own production facilities, making branded 'GrainParcel' storecupboard health foods.
Ideally encorporate the colours green and orange into the deck to match our logo. Please include some data on the health food sector, it is growing year on year, and customers wanting to shop local.

Please look at the attached pdf draft deck for more information on the business and do not hesitate to get in touch if you have any questions/require anything more from us.

Target Market(s)

Suppliers, financial constitutions, brands, investors

Industry/Entity Type

Retail

Font styles to use
Serif

Colors
00AB8E
00BBA5
67D7C9
C6EFE9
E9F9F6
F0912C
F2A743
F7CA91
FBE8D2
FDF5EE

Requirements
Must have
• Photos of the three stores, websites & their domain names

```html
<!DOCTYPE html>
<html lang="en">
<head>
<meta charset="utf-8">
<title>Meadow Pantry – Brand Presentation</title>
<link href="https://fonts.googleapis.com/css2?family=Playfair+Display:wght@600;700&family=Poppins:wght@400;600;700&display=swap" rel="stylesheet">
<style>
:root{
  --page:#f3d9b6;
  --cream:#fbe7d3;
  --green:#1f4b38;
  --green-2:#2f6a3f;
  --orange:#ec7434;
  --white:#ffffff;
  --ink:#2a3a30;
}
*{margin:0;padding:0;box-sizing:border-box}
html,body{width:842px;height:1200px;overflow:hidden;background:var(--page)}
body{position:relative;font-family:'Poppins',sans-serif;color:var(--ink)}
.slide{position:absolute;width:329px;height:185px;overflow:hidden;background:var(--cream);box-shadow:0 6px 16px rgba(120,80,40,.18)}
.col-l{left:73px}.col-r{left:440px}
.row1{top:56px}.row2{top:282px}.row3{top:508px}.row4{top:733px}.row5{top:959px}
.abs{position:absolute}
.serif{font-family:'Playfair Display',serif}
.heading{font-family:'Playfair Display',serif;font-weight:700;color:var(--green);font-size:12px;line-height:1}
.subhead{font-family:'Playfair Display',serif;color:var(--green);font-size:6px;margin-top:2px}
.rule{width:28px;height:1.5px;background:var(--orange);margin-top:3px}
.footer{position:absolute;left:11px;bottom:6px;font-family:'Playfair Display',serif;font-size:3.4px;color:var(--green)}
.page-no{position:absolute;right:8px;bottom:5px;width:6px;height:6px;border-radius:50%;background:var(--orange)}
.photo{position:absolute}
.tiny{font-size:3.4px;line-height:1.45}
/* stat cards */
.card{position:absolute;width:52px;height:49px;border-radius:2px;display:flex;flex-direction:column;align-items:center;justify-content:center;text-align:center;padding:10px 3px 3px}
.card.light{background:var(--white);box-shadow:0 2px 4px rgba(0,0,0,.12)}
.card.dark{background:var(--green);color:var(--white)}
.card .big{font-weight:700;font-size:5px;color:var(--orange);line-height:1.1}
.card .lbl{font-weight:700;font-size:4.6px;line-height:1.15;text-transform:uppercase}
.card.light .lbl{color:var(--green)}
.card .small{font-size:3.2px;line-height:1.3;margin-top:1px}
.card.outlined{border:.6px solid var(--orange)}
.icon{position:absolute;top:-8px;left:50%;margin-left:-8px;width:16px;height:16px;border-radius:50%;display:flex;align-items:center;justify-content:center}
.icon.or{background:var(--orange)}
.icon.gr{background:var(--green)}
.icon svg{width:9px;height:9px}
.dot-logo{width:20px;height:20px;border-radius:50%;background:var(--cream);border:.8px solid var(--orange);flex:none}
</style>
</head>
<body>

<!-- 1 · Title -->
<section class="slide col-l row1">
  <svg class="abs" width="329" height="185" style="left:0;top:0"><polygon points="231,0 329,0 329,185 189,185" fill="var(--green)"/></svg>
  <div class="abs" style="left:26px;top:40px;display:flex;gap:6px;align-items:center;font-family:'Playfair Display',serif;font-weight:700;color:var(--green);font-size:4.6px">
    <span style="display:flex;align-items:center;gap:2px"><span style="width:6px;height:6px;border-radius:50%;background:var(--orange)"></span>Meadow Pantry</span>
    <span>VitalCrateHub</span>
    <span>GrainParcel</span>
  </div>
  <div class="abs" style="left:20px;top:86px;width:120px;text-align:center">
    <div class="heading" style="font-size:12.5px">Meadow Pantry</div>
    <div class="serif" style="color:var(--green);font-size:9px;line-height:1.25;margin-top:2px">A Modern Challenger<br>in Health Retail</div>
    <div class="rule" style="margin:3px auto 0"></div>
  </div>
  <div class="abs serif" style="left:23px;top:169px;font-size:4.2px;color:var(--green);display:flex;gap:11px">
    <span>● grainparcel.co.uk</span><span>● vitalcratehub.co.uk</span>
  </div>
  <div class="photo" role="img" aria-label="Meadow Pantry Hackney shopfront" style="left:193px;top:20px;width:58px;height:58px;border-radius:50%;border:1px solid var(--orange);background:radial-gradient(circle,#6e8a8a,#2c3d44)"></div>
  <div class="photo" role="img" aria-label="Crates of fresh tomatoes" style="left:255px;top:50px;width:47px;height:47px;border-radius:50%;border:1px solid var(--orange);background:radial-gradient(circle,#c0442e,#5e6b3c)"></div>
  <div class="photo" role="img" aria-label="Kings Cross store interior" style="left:168px;top:82px;width:78px;height:78px;border-radius:50%;border:1px solid #8fae5a;background:radial-gradient(circle,#a46b45,#3a2d25)"></div>
  <div class="photo" role="img" aria-label="Clapham store window display" style="left:256px;top:111px;width:55px;height:55px;border-radius:50%;border:1px solid var(--orange);background:radial-gradient(circle,#8c94a8,#2c3346)"></div>
</section>

<!-- 2 · Who are we -->
<section class="slide col-r row1">
  <div class="abs heading" style="left:20px;top:28px;font-weight:600">WHO ARE WE?</div>
  <div class="abs" style="left:20px;top:41px;width:38px;height:1px;background:var(--orange)"></div>
  <ul class="abs tiny" style="left:20px;top:62px;width:104px;list-style:none;font-weight:600;color:var(--green)">
    <li style="padding-left:6px;position:relative;margin-bottom:8px"><span style="position:absolute;left:0;top:1px;width:2px;height:2px;background:var(--orange)"></span>Over the past 7 years we have grown from a humble family-run organic grocers in Hackney to a wholefoods business with three London locations and two online platforms.</li>
    <li style="padding-left:6px;position:relative"><span style="position:absolute;left:0;top:1px;width:2px;height:2px;background:var(--orange)"></span>Our ethos through out this growth has remained focused on providing healthy, well-made, well-grown food to our customers as well as working with the most exciting small brands in the sector.</li>
  </ul>
  <svg class="abs" width="329" height="185" style="left:0;top:0">
    <defs><linearGradient id="produce" x1="0" y1="0" x2="1" y2="1"><stop offset="0" stop-color="#5d7a3c"/><stop offset=".55" stop-color="#b5552f"/><stop offset="1" stop-color="#7d2a25"/></linearGradient></defs>
    <polygon points="126,0 182,0 182,62" fill="var(--green)"/>
    <polygon points="168,185 182,62 212,185" fill="var(--orange)"/>
    <polygon points="182,0 329,0 329,185 212,185 182,62" fill="url(#produce)" role="img" aria-label="Store shelves stacked with fresh fruit and vegetables"/>
  </svg>
  <div class="footer">Meadow Pantry</div>
  <div class="page-no"></div>
</section>

<!-- 3 · Our Story -->
<section class="slide col-l row2">
  <div class="abs" style="left:219px;top:0;width:110px;height:99px;background:var(--green)"></div>
  <div class="abs" style="left:24px;top:11px">
    <div class="heading">Our Story</div>
    <div class="subhead">From Local Roots to London Wide Recognition</div>
    <div class="rule" style="width:20px"></div>
  </div>
  <div class="card light" style="left:24px;top:53px"><span class="icon gr"><svg viewBox="0 0 10 10"><path d="M2 7h6M5 2v5M3 4l2-2 2 2" stroke="#fff" stroke-width="1" fill="none"/></svg></span><div class="big">Founded as<br>Meadow Fresh</div><div class="small" style="color:var(--green);font-weight:600">in Hackney (2018)</div></div>
  <div class="card dark" style="left:93px;top:53px"><span class="icon or"><svg viewBox="0 0 10 10"><path d="M2 4h6v4H2zM1.5 4l1-2h5l1 2" stroke="#fff" stroke-width=".9" fill="none"/></svg></span><div class="big">3 stores</div><div class="small">Hackney, Clapham<br>Kings Cross</div></div>
  <div class="card dark" style="left:24px;top:118px"><span class="icon or"><svg viewBox="0 0 10 10"><path d="M1.5 2.5h7v5h-7zM3 5h4" stroke="#fff" stroke-width=".9" fill="none"/></svg></span><div class="big">2 online sites</div><div class="small">grainparcel.co.uk<br>vitalcratehub.co.uk</div></div>
  <div class="card light" style="left:93px;top:118px"><span class="icon gr"><svg viewBox="0 0 10 10"><circle cx="5" cy="5" r="3" stroke="#fff" stroke-width=".9" fill="none"/></svg></span><div class="big">£4M</div><div class="small" style="color:var(--green);font-weight:600">Turnover</div></div>
  <div class="photo" role="img" aria-label="Wooden crates of tomatoes and vegetables in store" style="left:180px;top:26px;width:121px;height:143px;background:linear-gradient(165deg,#6f8a4a 0%,#9a5a3a 35%,#c2382a 65%,#7a3a2a 100%)"></div>
  <div class="footer">Meadow Pantry</div>
  <div class="page-no"></div>
</section>

<!-- 4 · Sales Channels -->
<section class="slide col-r row2" role="img" aria-label="Green farm fields under blue sky" style="background:linear-gradient(180deg,#8cb6d8 0%,#b7d3d9 22%,#5d8f3a 40%,#2f6a2a 100%)">
  <div class="abs" style="left:0;width:329px;top:12px;text-align:center">
    <div class="heading">Sales Channels Overview</div>
    <div class="rule" style="margin:3px auto 0"></div>
  </div>
  <div class="abs" style="left:24px;top:38px;width:151px;height:132px;background:var(--white);border-radius:2px;padding:8px 6px">
    <div style="font-weight:600;color:var(--orange);font-size:6.4px">BRICK AND MORTAR</div>
    <div style="display:flex;gap:5px;margin-top:5px"><div class="dot-logo" style="width:25px;height:25px"></div><div class="tiny" style="color:var(--green)"><b>Meadow Fresh, E9 2QX</b> our founder Dario began this family run buisness in the heart of Victoria Park Village in 2018 and watched it blossom into a favourite of the community</div></div>
    <div style="display:flex;gap:5px;margin-top:5px"><div class="dot-logo" style="width:25px;height:25px"></div><div class="tiny" style="color:var(--green)"><b>Meadow Pantry, SW4 9PL</b> our second store opened in 2021 and is located outside Clapham Common tube station. Here we work closely with reputable brands to create window displays and run sampling events</div></div>
    <div style="display:flex;gap:5px;margin-top:5px"><div class="dot-logo" style="width:25px;height:25px"></div><div class="tiny" style="color:var(--green)"><b>Meadow Pantry N1 4RT</b> our third store (opened 2024), a stones throw from Kings Cross station on the bustling Caledonian Road, expanded our capatilities as a business to include a cafe.</div></div>
  </div>
  <div class="abs" style="left:183px;top:38px;width:120px;height:132px;background:var(--white);border-radius:2px;padding:8px 6px">
    <div style="font-weight:600;color:var(--orange);font-size:6.4px">ONLINE</div>
    <div style="display:flex;gap:4px;margin-top:5px"><div class="dot-logo" style="width:26px;height:26px"></div><div class="tiny" style="color:var(--green)"><b>GrainParcel</b> created in 2022 is an online marketplace selling fresh produce, frozen and ambient goods as well as a selection of store cupboard products and supplements.</div></div>
    <div style="display:flex;gap:4px;margin-top:5px"><div class="dot-logo" style="width:26px;height:26px"></div><div class="tiny" style="color:var(--green)"><b>VitalCrateHub</b> was aquired in 2023 and specialises in a wide range of vitamins, supplements and health products.</div></div>
    <div class="tiny" style="margin-top:8px;background:var(--orange);color:#fff;font-weight:600;text-align:center;border-radius:2px;padding:4px 6px">Both online business are run out of our warehouse attached to our Kings Cross branch.</div>
  </div>
  <div class="footer" style="color:#fff">Meadow Pantry</div>
  <div class="page-no"></div>
</section>

<!-- 5 · Brand Partnerships -->
<section class="slide col-l row3">
  <div class="abs" role="img" aria-label="Soft-focus fresh produce on market stall" style="left:0;top:0;width:329px;height:85px;background:linear-gradient(180deg,#efe5d8 0%,#e6c7b0 55%,#d3b99a 100%);opacity:.9"></div>
  <div class="abs" style="left:0;top:85px;width:329px;height:100px;background:var(--green)"></div>
  <div class="abs" style="left:0;width:329px;top:12px;text-align:center">
    <div class="heading">Brand Partnerships</div>
    <div class="rule" style="margin:3px auto 0"></div>
  </div>
  <div class="photo" role="img" aria-label="Staff member outside store" style="left:23px;top:53px;width:58px;height:58px;border-radius:50%;border:1px solid var(--orange);background:radial-gradient(circle,#7a8d94,#2c3d44)"></div>
  <div class="photo" role="img" aria-label="Partner brand window display" style="left:98px;top:53px;width:58px;height:58px;border-radius:50%;border:1px solid var(--orange);background:radial-gradient(circle,#98a2b8,#334058)"></div>
  <div class="photo" role="img" aria-label="Seasonal shop window" style="left:173px;top:53px;width:58px;height:58px;border-radius:50%;border:1px solid var(--orange);background:radial-gradient(circle,#b95048,#3a3a3a)"></div>
  <div class="photo" role="img" aria-label="Refill station shelving" style="left:248px;top:53px;width:58px;height:58px;border-radius:50%;border:1px solid var(--orange);background:radial-gradient(circle,#b07a52,#3c2a22)"></div>
  <div class="abs" style="left:12px;top:121px;width:305px;display:flex;color:#fff;text-align:center">
    <div style="flex:1;padding:0 4px"><div style="color:var(--orange);font-weight:700;font-size:4.8px;line-height:1.1">TRUSTED<br>COLLABORATOR</div><div class="tiny" style="margin-top:3px">Meadow Pantry has cemeted its self as a trusted partner for international brands to advertise with</div></div>
    <div style="flex:1;padding:0 4px;border-left:.5px dashed #7a9a86"><div style="color:var(--orange);font-weight:700;font-size:4.8px;line-height:1.1">NO COMPROMISE<br>ON QUALITY</div><div class="tiny" style="margin-top:3px">Meadow Pantry has cemeted its self as a trusted partner for international brands to advertise with</div></div>
    <div style="flex:1;padding:0 4px;border-left:.5px dashed #7a9a86"><div style="color:var(--orange);font-weight:700;font-size:4.8px;line-height:1.1">COMMITMENT TO<br>SUSTAINABILITY</div><div class="tiny" style="margin-top:3px">Ethical and sustainable business practice underpins everything we do. From the brands we partner with, to our successful Save The Surplus programs, to our Purlia re-use and refill stations.</div></div>
    <div style="flex:1;padding:0 4px;border-left:.5px dashed #7a9a86"><div style="color:var(--orange);font-weight:700;font-size:4.8px;line-height:1.1">SMALL BUSINESS<br>INCUBATOR</div><div class="tiny" style="margin-top:3px">Meadow Pantry consistently works with up and coming local small businesses, stimulating growth and building a community</div></div>
  </div>
  <div class="footer" style="color:#fff">Meadow Pantry</div>
  <div class="page-no"></div>
</section>

<!-- 6 · Growth Vision -->
<section class="slide col-r row3" role="img" aria-label="Hand watering a young seedling in soil" style="background:radial-gradient(ellipse at 30% 55%,#7fb04a 0%,#2f6a32 40%,#153a26 100%)">
  <div class="abs" style="left:131px;top:29px">
    <div class="heading" style="color:#fff">Our Growth Vision</div>
    <div class="rule"></div>
  </div>
  <div class="abs" style="left:131px;top:55px;width:190px;display:flex;color:#fff">
    <div style="width:55px;padding-right:4px">
      <div style="width:14px;height:14px;border-radius:50%;background:var(--orange);margin-bottom:4px"></div>
      <div style="font-weight:700;font-size:4.8px;line-height:1.1">EXPAND OUR<br>CHAIN</div>
      <div class="tiny" style="margin-top:3px">Over the next 5 years we will open more brick-and mortar sites in a sprawling set on London locations.</div>
    </div>
    <div style="width:65px;padding:0 4px;border-left:.5px dashed #8ab08c">
      <div style="width:14px;height:14px;border-radius:50%;background:var(--orange);margin-bottom:4px"></div>
      <div style="font-weight:700;font-size:4.8px;line-height:1.1">ONLINE<br>PRODUCTION</div>
      <div class="tiny" style="margin-top:3px">We plan to begin in-house production of essential store cupboard goods, delivered by our own fleet of drivers, to create a more transparent, sustainable and high-end service for our customers.</div>
    </div>
    <div style="width:66px;padding-left:4px;border-left:.5px dashed #8ab08c">
      <div style="width:14px;height:14px;border-radius:50%;background:var(--orange);margin-bottom:4px"></div>
      <div style="font-weight:700;font-size:4.8px;line-height:1.1">INCREASE SUPPORT<br>FOR SMALL BUSINESS</div>
      <div class="tiny" style="margin-top:3px">2025 marks the start of our in-store seminar events for the brands we work with. These will including talks on social media presence, securing investement and in-store activations as well as further deepening the community around our stores.</div>
    </div>
  </div>
  <div class="footer" style="color:#fff">Meadow Pantry</div>
  <div class="page-no"></div>
</section>

<!-- 7 · Customer Base -->
<section class="slide col-l row4">
  <div class="abs" style="left:24px;top:11px">
    <div class="heading">Our Customer Base</div>
    <div class="subhead">Who Shops With Us?</div>
    <div class="rule"></div>
  </div>
  <div class="card light outlined" style="left:24px;top:56px"><span class="icon or"><svg viewBox="0 0 10 10"><circle cx="5" cy="3.5" r="1.6" stroke="#fff" stroke-width=".9" fill="none"/><path d="M2 9c0-2 1.5-3 3-3s3 1 3 3" stroke="#fff" stroke-width=".9" fill="none"/></svg></span><div class="lbl">Young<br>Professionals</div></div>
  <div class="card dark" style="left:93px;top:56px"><span class="icon or"><svg viewBox="0 0 10 10"><path d="M1.5 5h7M2.5 3.5v3M7.5 3.5v3" stroke="#fff" stroke-width="1" fill="none"/></svg></span><div class="lbl">Health<br>Conscious<br>Gym Goers</div></div>
  <div class="card dark" style="left:24px;top:121px"><span class="icon or"><svg viewBox="0 0 10 10"><circle cx="3.5" cy="3" r="1.2" stroke="#fff" stroke-width=".8" fill="none"/><circle cx="6.5" cy="3" r="1.2" stroke="#fff" stroke-width=".8" fill="none"/><path d="M2 9V6h3v3M5 9V6h3v3" stroke="#fff" stroke-width=".8" fill="none"/></svg></span><div class="lbl">Young<br>Families</div></div>
  <div class="card light outlined" style="left:93px;top:121px"><span class="icon or"><svg viewBox="0 0 10 10"><path d="M1.5 5h7a3.5 3.5 0 0 1-7 0zM5 2v2" stroke="#fff" stroke-width=".9" fill="none"/></svg></span><div class="lbl">Foodies</div></div>
  <div class="photo" role="img" aria-label="Shopper holding a basket of fresh produce" style="left:168px;top:17px;width:146px;height:152px;border-radius:2px;background:linear-gradient(160deg,#4d7fb0 0%,#c9a890 40%,#2f8a86 75%,#9a6a3a 100%)"></div>
  <div class="footer">Meadow Pantry</div>
  <div class="page-no"></div>
</section>

<!-- 8 · Health Food Boom -->
<section class="slide col-r row4">
  <div class="photo" role="img" aria-label="Rows of crops in a field at sunset" style="left:0;top:0;width:139px;height:185px;background:linear-gradient(180deg,#e9e3da 0%,#f1c77a 38%,#7a6a3a 52%,#2f4a22 75%,#1e2e18 100%)"></div>
  <div class="abs" style="left:150px;top:23px">
    <div class="heading">The Health Food Boom</div>
    <div class="subhead">UK Health Food Market</div>
    <div class="rule"></div>
  </div>
  <div class="abs" style="left:150px;top:66px;width:170px;display:grid;grid-template-columns:80px 80px;row-gap:17px;column-gap:0">
    <div style="display:flex;gap:4px"><div style="width:22px;height:22px;border-radius:50%;background:var(--green);flex:none"></div><div><div style="color:var(--orange);font-weight:700;font-size:9px;line-height:1">6–8%</div><div class="tiny" style="color:var(--green)">Annual growth<br>in the UK health<br>food sector</div></div></div>
    <div style="display:flex;gap:4px"><div style="width:22px;height:22px;border-radius:50%;background:var(--green);flex:none"></div><div><div style="color:var(--orange);font-weight:700;font-size:9px;line-height:1">73%</div><div class="tiny" style="color:var(--green)">Of UK shoppers prefer<br>brands with ethical &amp;<br>sustainable practices</div></div></div>
    <div style="display:flex;gap:4px"><div style="width:22px;height:22px;border-radius:50%;background:var(--green);flex:none"></div><div><div style="color:var(--orange);font-weight:700;font-size:9px;line-height:1">67%</div><div class="tiny" style="color:var(--green)">consumers actively<br>choose local or<br>organic products</div></div></div>
    <div style="display:flex;gap:4px"><div style="width:22px;height:22px;border-radius:50%;background:var(--green);flex:none"></div><div><div style="color:var(--orange);font-weight:700;font-size:9px;line-height:1">60%</div><div class="tiny" style="color:var(--green)">of consumers are<br>influenced by plastic-free<br>and refillable packaging</div></div></div>
  </div>
  <div class="footer" style="color:#fff">Meadow Pantry</div>
  <div class="page-no"></div>
</section>

<!-- 9 · Better Retailer -->
<section class="slide col-l row5">
  <div class="abs" style="left:230px;top:0;width:99px;height:185px;background:var(--green)"></div>
  <div class="abs" style="left:30px;top:21px">
    <div class="heading">A Better Kind of Retailer</div>
    <div class="subhead">We're not just a store – we're a platform</div>
    <div class="rule"></div>
  </div>
  <div class="card dark" style="left:30px;top:69px;width:62px"><span class="icon or"><svg viewBox="0 0 10 10"><circle cx="5" cy="5" r="3" stroke="#fff" stroke-width=".9" fill="none"/></svg></span><div class="lbl">Supporting<br>local makers,<br>community health,<br>and eco-living</div></div>
  <div class="card dark" style="left:103px;top:69px;width:52px"><span class="icon or"><svg viewBox="0 0 10 10"><path d="M2 4h6v4H2zM1.5 4l1-2h5l1 2" stroke="#fff" stroke-width=".9" fill="none"/></svg></span><div class="lbl">Creating<br>a retail<br>experience<br>that cares</div></div>
  <div class="abs" style="left:30px;top:126px;width:126px;height:37px;background:var(--orange);border-radius:2px;display:flex;align-items:center;justify-content:center;text-align:center;color:#fff;font-weight:700;font-size:4.6px;line-height:1.2">"WE'RE BUILDING SOMETHING DIFFERENT<br>WHERE YOUR SHOPPING<br>BASKET REFLECTS YOUR VALUES."</div>
  <div class="photo" role="img" aria-label="Customer ordering groceries online at home" style="left:184px;top:47px;width:145px;height:116px;background:linear-gradient(135deg,#e7ddd0 0%,#c7b8a6 45%,#5d7fa8 70%,#c8a57a 100%)"></div>
  <div class="footer">Meadow Pantry</div>
  <div class="page-no"></div>
</section>

<!-- 10 · Thank You -->
<section class="slide col-r row5" style="background:var(--green);color:#fff;text-align:center">
  <div class="abs" style="left:0;width:329px;top:56px">
    <div class="serif" style="color:var(--orange);font-weight:700;font-size:15px">Thank You</div>
    <div style="font-size:5.6px;margin-top:5px">info@meadowpantry.co.uk</div>
    <div style="font-size:5.6px;font-weight:700;margin-top:3px">HACKNEY <span style="color:var(--orange)">|</span> CLAPHAM <span style="color:var(--orange)">|</span> KINGS CROSS</div>
    <div style="font-size:5.6px;margin-top:9px">www.grainparcel.co.uk</div>
    <div style="font-size:5.6px;margin-top:3px">www.vitalcratehub.co.uk</div>
  </div>
</section>

</body>
</html>
```